BRV Early College and Career Program

Starting a new program initiative at Birchmont Valley School where students will have the opportunity to take college courses during their senior year of high school. Preferably add some pictures to reflect the career pathways we are offering (below) Some context to use for this flyer are:

Learn more about the career focused courses in…
• Education
• Computer & Information Science
• Technology & Engineering
• Health

Things to look forward to:
Experience college in high school
Finish college early
Save money on college tuition and fees
Advice on Career pathways

all classes fit into OPAL CREDIT BUNDLE

For more information contact

Gavin Purdy - ZT12 Alliances -WHVC
555.014.2291
Email: gpurdy@whvc-example.edu

Ms. Okafuji- Early College Coordinator
Email: dena.okafuji@birchmont-example.org
Room J215

I uploaded 5 or so photos that I would like to see incorporated in the design of the flier- using real students from our high school will give a more realistic approach- thanks, Added Monday, August 21, 2017

Target Market(s)

High school students who are currently in 10th grade (for recruitment) and only high school juniors and seniors are able to apply.

Industry/Entity Type

School

Colors

Designer to choose colors to be used in the design.

Requirements
Must have
• logos- some pictures reflecting the different career pathways and the contact information provided. Looking to also have this in a format that I can print on card stock paper not just full length page- ADD / USE photos attached to see which one fits the project better.
Nice to have
• suitable for high school students- attractive
Should not have
• Do not include any generic phone numbers.

```html
<!DOCTYPE html>
<html lang="en">
<head>
<meta charset="utf-8">
<title>BRV Early College and Career Program</title>
<link rel="stylesheet" href="https://fonts.googleapis.com/css2?family=Source+Sans+3:wght@400;600;700&display=swap">
<style>
  :root {
    --navy: #1b3765;
    --blue: #3f7cc4;
    --blue-light: #5b8fd0;
    --blue-pale: #9fbfe6;
    --ring: #d4d6da;
    --grey-text: #6d6e71;
    --contact-text: #dfe5ef;
    --white: #ffffff;
    --photo-a: #6b5a52;
    --photo-b: #2a2c3a;
  }
  * { box-sizing: border-box; margin: 0; padding: 0; }
  html, body { width: 936px; height: 1200px; overflow: hidden; background: var(--white); }
  body { font-family: "Source Sans 3", Arial, sans-serif; position: relative; }
  .backdrop { position: absolute; inset: 0; }
  .photo { position: absolute; left: 11px; top: 11px; width: 575px; height: 495px;
    clip-path: polygon(0 0, 290px 0, 575px 495px, 0 495px);
    background: linear-gradient(135deg, var(--photo-a), var(--photo-b)); }

  .brand { position: absolute; color: var(--navy); font-weight: 700; line-height: 1.1; white-space: nowrap; }
  .brand-school { left: 443px; top: 82px; font-size: 19px; display: flex; align-items: center; gap: 9px; letter-spacing: 0.3px; }
  .brand-school .mark { width: 20px; height: 20px; background: var(--navy); flex: none; }
  .brand-college { left: 690px; top: 80px; font-size: 20px; }

  .title { position: absolute; left: 430px; top: 232px; width: 495px; text-align: center;
    color: var(--white); font-weight: 700; font-size: 37px; line-height: 1.22; }
  .subtitle { position: absolute; left: 556px; top: 381px; width: 340px; text-align: center;
    color: var(--navy); font-weight: 700; font-size: 20px; line-height: 1.3; }

  .perks { position: absolute; left: 43px; top: 528px; }
  .perks h2 { color: var(--navy); font-size: 17px; font-weight: 700; margin-bottom: 3px; }
  .perks ul { list-style: none; }
  .perks li { color: var(--grey-text); font-size: 19px; line-height: 28.5px; display: flex; align-items: center; gap: 10px; }
  .perks li::before { content: ""; width: 11px; height: 11px; border-radius: 50%; background: var(--blue); flex: none; }

  .pathway-label { position: absolute; color: var(--white); font-weight: 600; font-size: 18.5px;
    text-align: center; line-height: 1.2; transform: translateX(-50%); white-space: nowrap; }

  .contact-tab { position: absolute; left: 516px; top: 904px; width: 409px; height: 45px;
    background: var(--blue-light); clip-path: polygon(20px 0, 100% 0, 100% 100%, 0 100%);
    color: var(--white); font-size: 18.5px; display: flex; align-items: center; justify-content: center; }

  .contact { position: absolute; top: 1015px; color: var(--contact-text); font-size: 16.5px; line-height: 25px; white-space: nowrap; }
  .contact .name { color: var(--white); font-size: 20.5px; font-weight: 600; line-height: 30px; }
  .contact .email { display: flex; align-items: center; gap: 6px; font-size: 15px; letter-spacing: -0.1px; }
  .contact .email svg { flex: none; }
</style>
</head>
<body>
  <svg class="backdrop" width="936" height="1200" viewBox="0 0 936 1200" aria-hidden="true">
    <polygon points="290,11 326,11 612,506 576,506" fill="var(--blue)"/>
    <polygon points="326,11 336,11 622,506 612,506" fill="var(--blue-pale)"/>
    <rect x="430" y="205" width="495" height="5" fill="var(--blue)"/>
    <rect x="430" y="214" width="495" height="136" fill="var(--navy)"/>
    <rect x="430" y="352" width="495" height="5" fill="var(--blue)"/>
    <polygon points="11,795 925,508 925,540 11,830" fill="var(--blue)"/>
    <polygon points="11,818 925,530 925,1151 11,1151" fill="var(--navy)"/>
    <rect x="11" y="1162" width="914" height="32" fill="var(--blue-light)"/>

    <g>
      <circle cx="138" cy="802" r="82" fill="var(--ring)"/>
      <circle cx="138" cy="802" r="72" fill="var(--blue-light)"/>
      <polygon points="138,770 190,790 138,810 86,790" fill="var(--white)"/>
      <path d="M106 800 v22 q32 16 64 0 v-22 l-32 12z" fill="var(--white)"/>
      <rect x="183" y="792" width="4" height="38" fill="var(--white)"/>
    </g>
    <g>
      <circle cx="365" cy="748" r="82" fill="var(--ring)"/>
      <circle cx="365" cy="748" r="72" fill="var(--blue-light)"/>
      <rect x="340" y="738" width="72" height="44" rx="3" fill="none" stroke="var(--white)" stroke-width="5"/>
      <rect x="330" y="784" width="92" height="6" fill="var(--white)"/>
      <circle cx="350" cy="724" r="14" fill="none" stroke="var(--white)" stroke-width="7" stroke-dasharray="5 4"/>
      <circle cx="322" cy="752" r="10" fill="none" stroke="var(--white)" stroke-width="6" stroke-dasharray="4 3"/>
    </g>
    <g>
      <circle cx="577" cy="667" r="82" fill="var(--ring)"/>
      <circle cx="577" cy="667" r="72" fill="var(--blue-light)"/>
      <circle cx="568" cy="667" r="28" fill="none" stroke="var(--white)" stroke-width="12" stroke-dasharray="8 6"/>
      <circle cx="568" cy="667" r="10" fill="var(--white)"/>
      <ellipse cx="590" cy="667" rx="30" ry="11" fill="none" stroke="var(--white)" stroke-width="3" transform="rotate(40 590 667)"/>
      <ellipse cx="590" cy="667" rx="30" ry="11" fill="none" stroke="var(--white)" stroke-width="3" transform="rotate(-40 590 667)"/>
    </g>
    <g>
      <circle cx="800" cy="581" r="82" fill="var(--ring)"/>
      <circle cx="800" cy="581" r="72" fill="var(--blue-light)"/>
      <rect x="792" y="540" width="16" height="82" rx="3" fill="var(--white)"/>
      <rect x="766" y="566" width="68" height="16" rx="3" fill="var(--white)"/>
    </g>
  </svg>

  <div class="photo" role="img" aria-label="Photo of two students standing beside a video camera on a tripod"></div>

  <div class="brand brand-school"><span class="mark"></span>BIRCHMONT VALLEY<br>PUBLIC SCHOOLS</div>
  <div class="brand brand-college">Westhaven Valley<br>Community College</div>

  <h1 class="title">BRV Early College and<br>Career Program</h1>
  <p class="subtitle">Take career focused courses at Westhaven Valley and earn credit for both college and high school</p>

  <section class="perks">
    <h2>EXPERIENCE COLLEGE WHILE IN HIGH SCHOOL :</h2>
    <ul>
      <li>Experience college while in high school</li>
      <li>Finish college early</li>
      <li>Save money on college tuition and fees</li>
      <li>Get advice on your future career</li>
    </ul>
  </section>

  <div class="pathway-label" style="left:138px; top:897px;">EDUCATION</div>
  <div class="pathway-label" style="left:365px; top:843px;">COMPUTER &amp;<br>INFORMATION SCIENCE</div>
  <div class="pathway-label" style="left:577px; top:762px;">ENGINEERING</div>
  <div class="pathway-label" style="left:800px; top:677px;">HEALTH</div>

  <div class="contact-tab">FOR MORE INFORMATION CONTACT</div>

  <div class="contact" style="left:43px;">
    <div class="name">Gavin Purdy</div>
    <div>Room J215</div>
    <div class="email"><svg width="15" height="10" viewBox="0 0 15 10"><rect width="15" height="10" fill="#8fb1dd"/><path d="M0 0 L7.5 6 L15 0" stroke="var(--navy)" fill="none"/></svg>gpurdy@whvc-example.edu</div>
  </div>
  <div class="contact" style="left:306px;">
    <div class="name">Ms. Okafuji</div>
    <div>Early College Coordinator</div>
    <div>Room J215</div>
    <div class="email"><svg width="15" height="10" viewBox="0 0 15 10"><rect width="15" height="10" fill="#8fb1dd"/><path d="M0 0 L7.5 6 L15 0" stroke="var(--navy)" fill="none"/></svg>dena.okafuji@birchmont-example.org</div>
  </div>
  <div class="contact" style="left:612px;">
    <div class="name">Ms. Valdivia</div>
    <div>Work-Based Learning Coordinator</div>
    <div>Room J215</div>
    <div class="email"><svg width="15" height="10" viewBox="0 0 15 10"><rect width="15" height="10" fill="#8fb1dd"/><path d="M0 0 L7.5 6 L15 0" stroke="var(--navy)" fill="none"/></svg>rina.valdivia@birchmont-example.org</div>
  </div>
</body>
</html>
```